Ductless Mini Split Business Website

Copper Fern Services is looking to design an eye catching educational website about installing Ductless mini splits.

Similar to this company.
https://www.halvikstream.com/

Coding

Coded - Design and coding required

```html
<!DOCTYPE html>
<html lang="en">
<head>
<meta charset="utf-8">
<title>Copper Fern Services – Ductless Experts</title>
<link href="https://fonts.googleapis.com/css2?family=Varela+Round&family=Open+Sans:wght@400;600;700&display=swap" rel="stylesheet">
<style>
:root{
  --yellow:#fcc50b;
  --yellow-dark:#d8b423;
  --ink:#1d1d1d;
  --text:#3a3a3a;
  --muted:#777;
  --line:#d6d6d6;
  --pale:#eef0f4;
  --footer:#141414;
  --white:#fff;
}
*{margin:0;padding:0;box-sizing:border-box}
html,body{width:1200px;height:4591px;overflow:hidden}
body{position:relative;background:var(--white);font-family:"Open Sans",sans-serif;color:var(--text)}
.abs{position:absolute}
h1,h2,h3,.round{font-family:"Varela Round",sans-serif;font-weight:400;color:var(--ink)}
.btn{position:absolute;background:var(--yellow);color:var(--ink);border-radius:22px;font-family:"Varela Round",sans-serif;font-size:15px;display:flex;align-items:center;justify-content:center;height:40px}

/* header */
.brand{left:145px;top:26px;display:flex;align-items:center;gap:10px}
.brand-dot{width:36px;height:36px;border-radius:50%;background:var(--yellow)}
.brand-name{font-family:"Varela Round",sans-serif;font-size:19px;color:var(--ink);line-height:1.15;width:150px}
.call{right:145px;top:24px;display:flex;align-items:center;gap:10px;font-family:"Varela Round",sans-serif;font-size:22px;color:var(--ink)}
.call-ico{width:36px;height:36px;border-radius:50%;background:var(--yellow);display:flex;align-items:center;justify-content:center}
.nav{right:145px;top:80px;display:flex;gap:33px;font-size:12px;color:#333}
.nav .on{text-decoration:underline}

/* hero */
.hero-img{left:0;top:120px;width:1200px;height:560px;background:linear-gradient(180deg,#7f8b93 0%,#6f7b84 55%,#4f5963 100%)}
.hero-title{left:145px;top:288px;font-size:47px}
.hero-sub{left:145px;top:356px;font-size:16px;color:#2a2a2a}
.arrow{width:42px;height:42px;border-radius:50%;background:#fff;display:flex;align-items:center;justify-content:center}

/* services */
.sec-title{width:1200px;left:0;text-align:center;font-size:38px}
.svc{width:297px;height:170px;border:1px solid var(--line);background:#fff;display:flex;flex-direction:column;align-items:center;justify-content:flex-end;padding-bottom:26px;font-size:18px;color:var(--ink)}
.svc svg{margin-bottom:26px}

/* about */
.about-bg{left:0;top:1403px;width:1200px;height:510px;background:var(--pale)}
.about-img{left:0;top:1403px;width:560px;height:510px;background:linear-gradient(135deg,#f3f4f6 0%,#dfe2e7 60%,#8aa0b8 100%)}
.about-title{left:595px;top:1456px;font-size:38px}
.about-text{left:595px;top:1512px;width:460px;font-size:11.5px;line-height:24px;color:#444}

/* features */
.feat-title{left:141px;top:1985px;font-size:38px}
.feat-intro{left:145px;top:2043px;width:450px;font-size:11.5px;line-height:24px;color:#444}
.feat{left:143px;display:flex;gap:18px;align-items:center}
.feat-ico{width:102px;height:102px;border-radius:50%;border:3px solid var(--yellow);background:#fff;flex:none;display:flex;align-items:center;justify-content:center}
.feat h3{font-family:"Open Sans",sans-serif;font-size:16px;font-weight:400;margin-bottom:4px}
.feat p{font-size:11px;line-height:18px;width:330px;color:#444}

/* contact */
.contact-bg{left:0;top:2560px;width:1200px;height:640px;background:var(--pale)}
.contact-sub{width:1200px;left:0;top:2690px;text-align:center;font-size:22px;font-family:"Varela Round",sans-serif;color:var(--ink)}
.contact-sub span{border-bottom:2px solid var(--yellow)}
.field{background:#fff;border:1px solid #bfc3c9;font-size:11px;color:#666;padding:0 16px;display:flex;align-items:center;height:40px}

/* reviews */
.quote{left:200px;top:3343px;width:800px;text-align:center;font-size:18px;line-height:32px;color:#444}
.quote-card{left:160px;top:3440px;width:880px;height:16px;box-shadow:0 12px 16px -10px rgba(0,0,0,.15)}
.author{width:1200px;left:0;top:3476px;text-align:center;color:var(--yellow-dark);font-family:"Varela Round",sans-serif;font-size:18px}
.author small{display:block;font-size:10px;color:#888;font-family:"Open Sans",sans-serif}

/* aenean */
.band-img{left:0;top:3595px;width:1200px;height:660px;background:linear-gradient(180deg,#a9bcca 0%,#d5dde3 40%,#e6e8ea 100%)}
.card{width:293px;height:262px;border:3px solid #fff;box-shadow:0 4px 10px rgba(0,0,0,.25);display:flex;align-items:flex-end;justify-content:center;padding-bottom:16px;font-family:"Varela Round",sans-serif;font-size:29px;color:var(--yellow)}

/* footer */
.footer{left:0;top:4200px;width:1200px;height:391px;background:var(--footer)}
.fcol h4{font-family:"Varela Round",sans-serif;font-weight:400;font-size:19px;color:var(--yellow);margin-bottom:14px}
.fcol li{list-style:none;font-size:9.5px;color:#aaa;line-height:24px;display:flex;gap:10px;align-items:center}
.social{width:44px;height:44px;border-radius:50%;border:1px solid #666;display:flex;align-items:center;justify-content:center}
.copy{left:145px;top:4548px;font-size:9.5px;color:#999}
.rule{left:145px;top:4525px;width:910px;height:1px;background:#333}
</style>
</head>
<body>

<!-- header -->
<div class="abs brand"><span class="brand-dot"></span><span class="brand-name">Copper Fern Services</span></div>
<div class="abs call"><span class="call-ico"><svg width="18" height="18" viewBox="0 0 24 24"><path fill="#1d1d1d" d="M6.6 10.8a15.1 15.1 0 0 0 6.6 6.6l2.2-2.2c.3-.3.7-.4 1-.2 1.1.4 2.3.6 3.6.6.6 0 1 .4 1 1V20c0 .6-.4 1-1 1A17 17 0 0 1 3 4c0-.6.4-1 1-1h3.5c.6 0 1 .4 1 1 0 1.3.2 2.5.6 3.6.1.3 0 .7-.2 1z"/></svg></span>Call us : 555 014 2278</div>
<nav class="abs nav"><span class="on">HOME</span><span>ABOUT US</span><span>DUCTLESS HEAT PUMPS</span><span>FINANCING</span><span>REVIEW</span><span>CONTACT US</span><span>FAQ</span></nav>

<!-- hero -->
<div class="abs hero-img" role="img" aria-label="Woman relaxing on a sofa under a wall-mounted ductless air conditioner"></div>
<svg class="abs" style="left:0;top:600px" width="1200" height="175" viewBox="0 0 1200 175"><path d="M0 20 C200 60 300 40 430 40 C620 40 740 170 900 150 C1040 130 1130 60 1200 20 V175 H0Z" fill="#fff"/><path d="M0 20 C200 60 300 40 430 40 C620 40 740 170 900 150 C1040 130 1130 60 1200 20 V40 C1120 90 1040 160 900 170 C740 175 620 70 430 60 C300 60 200 80 0 40Z" fill="var(--yellow)"/></svg>
<h1 class="abs hero-title">Aliquam erat volutpat</h1>
<p class="abs hero-sub">Etiam mattis augue vehicula odio posuere tempus lectus luctus</p>
<div class="btn" style="left:145px;top:392px;width:121px">Read More</div>
<div class="abs arrow" style="left:46px;top:346px"><svg width="14" height="14" viewBox="0 0 14 14"><path d="M9 2 4 7l5 5" stroke="#111" stroke-width="2.4" fill="none"/></svg></div>
<div class="abs arrow" style="left:1110px;top:346px"><svg width="14" height="14" viewBox="0 0 14 14"><path d="m5 2 5 5-5 5" stroke="#111" stroke-width="2.4" fill="none"/></svg></div>

<!-- services -->
<h2 class="abs sec-title" style="top:838px">Copper Fern Services</h2>
<div class="abs svc" style="left:145px;top:902px"><svg width="70" height="46" viewBox="0 0 70 46" fill="none" stroke="#222" stroke-width="2"><rect x="3" y="3" width="64" height="22" rx="3"/><path d="M10 19h50M20 32l-3 10M30 32v10M40 32v10M50 32l3 10"/></svg>Ductless Installation</div>
<div class="abs svc" style="left:451px;top:902px"><svg width="70" height="66" viewBox="0 0 70 66" fill="none" stroke="#222" stroke-width="2"><rect x="3" y="3" width="64" height="22" rx="3"/><path d="M10 19h50M27 32v10M35 32v10M43 32v10M12 48l12 12M24 48 12 60M18 46v16M46 48l12 12M58 48 46 60M52 46v16"/></svg>Ductless Maintenance</div>
<div class="abs svc" style="left:757px;top:902px"><svg width="66" height="66" viewBox="0 0 66 66" fill="none" stroke="#222" stroke-width="2"><path d="M8 8l12 4 30 30 6 0 8 8-6 6-8-8 0-6L20 12zM50 4c6 0 12 6 10 12l-8 8-10-2-2-10zM24 40 6 58l4 4 18-18"/></svg>Ductless Repairs</div>
<div class="abs svc" style="left:145px;top:1080px"><svg width="70" height="66" viewBox="0 0 70 66" fill="none" stroke="#222" stroke-width="2"><path d="M6 4h36v58H6zM12 14h24M12 22h24M12 30h18M12 50h18M48 30l12 4v12c0 8-6 12-12 16-6-4-12-8-12-16V34z"/></svg>Ductless Warranty</div>
<div class="abs svc" style="left:451px;top:1080px"><svg width="70" height="66" viewBox="0 0 70 66" fill="none" stroke="#222" stroke-width="2"><path d="M35 4 4 30h8v32h46V30h8zM48 12V6h6v12M35 28v24M25 34l20 12M45 34 25 46"/></svg>Whole House Ductless</div>
<div class="abs svc" style="left:757px;top:1080px"><svg width="70" height="66" viewBox="0 0 70 66" fill="none" stroke="#222" stroke-width="2"><path d="M6 6h12v56H6zM10 14h4M10 26h4M10 38h4M10 50h4M26 20h26a6 6 0 1 0-6-6M26 32h34a6 6 0 1 1-6 6M26 44h18a6 6 0 1 1-6 6"/></svg>Ductless For Remodels</div>
<div class="btn" style="left:504px;top:1271px;width:192px">View More Services</div>

<!-- about -->
<div class="abs about-bg"></div>
<div class="abs about-img" role="img" aria-label="Technician servicing a wall-mounted ductless unit"></div>
<svg class="abs" style="left:0;top:1820px" width="1200" height="100" viewBox="0 0 1200 100"><path d="M0 40 C150 80 350 80 500 60 C700 30 800 20 950 30 C1050 36 1130 20 1200 10 V100 H0Z" fill="#fff"/><path d="M0 40 C150 80 350 80 500 60 C700 30 800 20 950 30 C1050 36 1130 20 1200 10 V20 C1130 30 1050 46 950 40 C800 32 700 44 500 70 C350 90 150 90 0 52Z" fill="var(--yellow)"/></svg>
<h2 class="abs about-title">About Copper Fern Services</h2>
<p class="abs about-text">Quisque aliquet ex nec est vestibulum pulvinar. Pellentesque convallis molestie enim sit amet efficitur. Etiam id imperdiet lectus. Vivamus lacus justo, ultrices nec erat in, euismod iaculis mauris. Vivamus eleifend vitae nulla vel malesuada. In ac malesuada lacus, et consectetur ante. Fusce vitae lectus sit amet mi pulvinar maximus. Aenean placerat, nibh vel accumsan aliquet, magna nibh accumsan nibh, ac tempus nunc ipsum ac tellus. Cras augue magna, placerat eget nulla non, congue suscipit neque. Etiam mattis augue vehicula odio posuere, sit amet tempus lectus luctus. Nulla facilisi. Etiam vel massa elementum, bibendum tellus venenatis, feugiat massa.</p>
<div class="btn" style="left:595px;top:1722px;width:121px">Read More</div>

<!-- features -->
<h2 class="abs feat-title">Fusce sollicitudin</h2>
<p class="abs feat-intro">Phasellus nisl est, condimentum vitae faucibus in, sollicitudin vel metus. Nunc sit amet consequat risus. Curabitur ac elit leo. In eleifend dui tellus, in scelerisque elit porttitor et. Integer eu massa lacinia, lacinia nulla non.</p>
<div class="abs feat" style="top:2134px"><div class="feat-ico"><svg width="40" height="46" viewBox="0 0 40 46" fill="none" stroke="#222" stroke-width="1.6"><path d="M6 4h22l8 8v30H6zM12 14h16M12 20h18M12 26h18M12 32h18"/></svg></div><div><h3>Aliquam erat volutpat</h3><p>Aenean feugiat viverra lorem ac sagittis. Donec sit amet lectus nec mi tempor laoreet ac nec nunc. Duis id auctor sapien.</p></div></div>
<div class="abs feat" style="top:2251px"><div class="feat-ico"><svg width="46" height="46" viewBox="0 0 46 46" fill="none" stroke="#222" stroke-width="1.6"><path d="M18 4h22v34H18zM4 26h12v16H4zM16 30h10l6 6M24 12h10M24 20h10"/></svg></div><div><h3>Mauris suscipit felis</h3><p>Aenean feugiat viverra lorem ac sagittis. Donec sit amet lectus nec mi tempor laoreet ac nec nunc. Duis id auctor sapien.</p></div></div>
<div class="abs feat" style="top:2376px"><div class="feat-ico"><svg width="46" height="46" viewBox="0 0 46 46" fill="none" stroke="#222" stroke-width="1.6"><circle cx="22" cy="24" r="16"/><path d="M14 22l8-8 12 12-8 8zM18 30l-6 6"/></svg></div><div><h3>Nullam accumsan purus</h3><p>Aenean feugiat viverra lorem ac sagittis. Donec sit amet lectus nec mi tempor laoreet ac nec nunc. Duis id auctor sapien.</p></div></div>
<div class="abs" style="left:657px;top:2013px;width:400px;height:400px;border-radius:50%;background:radial-gradient(circle at 70% 45%,#f4e7b5 0%,#d8b423 55%,#c9a51d 100%)" role="img" aria-label="Circular heating and cooling emblem illustration"></div>
<div class="abs" style="left:712px;top:2425px;width:290px;height:16px;border-radius:50%;background:radial-gradient(ellipse,rgba(0,0,0,.25),rgba(0,0,0,0) 70%)"></div>

<!-- contact -->
<div class="abs contact-bg"></div>
<h2 class="abs sec-title" style="top:2630px">Contact Us</h2>
<p class="abs contact-sub">Mauris suscipit felis elementum varius <span>555 014 2279</span></p>
<div class="abs field" style="left:352px;top:2742px;width:238px">Name</div>
<div class="abs field" style="left:609px;top:2742px;width:239px">Email</div>
<div class="abs field" style="left:352px;top:2798px;width:238px">Phone</div>
<div class="abs field" style="left:609px;top:2798px;width:239px;justify-content:space-between">Are you a new customer?<svg width="10" height="6" viewBox="0 0 10 6"><path d="m1 1 4 4 4-4" stroke="#333" stroke-width="1.5" fill="none"/></svg></div>
<div class="abs field" style="left:352px;top:2855px;width:496px;height:127px;align-items:flex-start;padding-top:14px">Message</div>
<div class="btn" style="left:540px;top:2999px;width:120px">Submit</div>
<svg class="abs" style="left:0;top:3110px" width="1200" height="110" viewBox="0 0 1200 110"><path d="M0 60 C200 20 350 0 560 20 C760 40 900 10 1200 40 V110 H0Z" fill="#fff"/><path d="M0 60 C200 20 350 0 560 20 C760 40 900 10 1200 40 V54 C900 24 760 56 560 36 C350 16 200 36 0 76Z" fill="var(--yellow)"/></svg>

<!-- reviews -->
<h2 class="abs sec-title" style="top:3280px">Reviews</h2>
<p class="abs quote">“ Phasellus blandit quam a ipsum gravida dapibus. Cras sed augue tortor. Suspendisse elit ligula, iaculis dignissim justo vestibulum venenatis elit. Sed egestas, nisl id cursus ultricies, turpis orci rhoncus odio, id tristique odio ex in lacus. ”</p>
<div class="abs quote-card"></div>
<svg class="abs" style="left:52px;top:3374px" width="26" height="30" viewBox="0 0 26 30"><path d="M18 3 6 15l12 12" stroke="#888" stroke-width="3" fill="none"/></svg>
<svg class="abs" style="left:1122px;top:3374px" width="26" height="30" viewBox="0 0 26 30"><path d="m8 3 12 12L8 27" stroke="#888" stroke-width="3" fill="none"/></svg>
<div class="abs author">Mara Linden<small>City name</small></div>

<!-- aenean -->
<div class="abs band-img" role="img" aria-label="Bright living room with a wall-mounted air conditioner"></div>
<div class="abs" style="left:975px;top:3510px;width:180px;height:190px;border-radius:50%;background:radial-gradient(circle,#f2cf3a 0%,#e2b41a 60%,rgba(226,180,26,0) 72%)" role="img" aria-label="Mascot illustration"></div>
<h2 class="abs sec-title" style="top:3765px">Aenean aliquet</h2>
<div class="abs card" style="left:145px;top:3850px;background:linear-gradient(180deg,#dfe3e6,#8c8f94)" role="img" aria-label="Woman on sofa with remote control">Have Questions?</div>
<div class="abs card" style="left:453px;top:3850px;background:linear-gradient(180deg,#c8d2d9,#5d6770)" role="img" aria-label="Woman standing below a ductless unit">Financing Options</div>
<div class="abs card" style="left:762px;top:3850px;background:linear-gradient(180deg,#b9a899,#7f7469)" role="img" aria-label="Woman relaxing beside a brick wall">Stay Up To Date</div>

<!-- footer -->
<svg class="abs" style="left:0;top:4155px" width="1200" height="90" viewBox="0 0 1200 90"><path d="M0 50 C250 70 450 70 650 60 C850 50 1050 20 1200 0 V90 H0Z" fill="var(--yellow)"/></svg>
<div class="abs footer"></div>
<svg class="abs" style="left:0;top:4160px" width="1200" height="90" viewBox="0 0 1200 90"><path d="M0 66 C250 86 450 86 650 76 C850 66 1050 36 1200 16 V90 H0Z" fill="var(--footer)"/></svg>
<div class="abs" style="left:145px;top:4300px;display:flex;align-items:center;gap:10px"><span class="brand-dot" style="width:30px;height:30px;border-radius:50%;background:var(--yellow);display:block"></span><span style="font-family:'Varela Round',sans-serif;font-size:17px;color:var(--yellow);width:140px;line-height:1.2">Copper Fern Services</span></div>
<div class="abs fcol" style="left:403px;top:4296px"><h4>Links</h4><ul><li>Home</li><li>About Us</li><li>Ductless Heat Pumps</li><li>Financing</li><li>Review</li><li>Contact us</li><li>FAQ</li></ul></div>
<div class="abs fcol" style="left:595px;top:4296px"><h4>Contact Us</h4><ul>
<li><svg width="10" height="12" viewBox="0 0 10 12"><path d="M5 0a4 4 0 0 0-4 4c0 3 4 8 4 8s4-5 4-8a4 4 0 0 0-4-4z" fill="#aaa"/></svg>24 Building name, Street name, City Zipcode</li>
<li><svg width="10" height="10" viewBox="0 0 24 24"><path fill="#aaa" d="M6.6 10.8a15.1 15.1 0 0 0 6.6 6.6l2.2-2.2c.3-.3.7-.4 1-.2 1.1.4 2.3.6 3.6.6.6 0 1 .4 1 1V20c0 .6-.4 1-1 1A17 17 0 0 1 3 4c0-.6.4-1 1-1h3.5c.6 0 1 .4 1 1 0 1.3.2 2.5.6 3.6.1.3 0 .7-.2 1z"/></svg>Phone : 555 014 2280</li>
<li><svg width="11" height="9" viewBox="0 0 11 9"><rect width="11" height="9" fill="#aaa"/><path d="m0 0 5.5 5L11 0" stroke="#141414" fill="none"/></svg>Email : hello@copperfern.example</li></ul></div>
<div class="abs fcol" style="left:897px;top:4296px"><h4>Follow us on</h4>
<div style="display:flex;gap:13px"><span class="social"></span><span class="social"></span><span class="social"></span></div></div>
<div class="abs rule"></div>
<p class="abs copy">Copyright © 2019 Copper Fern Services. All rights reserved.</p>
<div class="abs" style="left:1024px;top:4538px;width:30px;height:30px;border-radius:50%;background:#555;display:flex;align-items:center;justify-content:center"><svg width="12" height="8" viewBox="0 0 12 8"><path d="m1 7 5-5 5 5" stroke="#141414" stroke-width="2" fill="none"/></svg></div>

</body>
</html>
```